Banner für Immobilienmakler
Zielgruppe
Immobilienmakler, Immobilienverkauf mit Herz,
Aufgabenstellung
Verkauf von Häusern und Wohnungen, der Banner soll an einen Balkon oder einen Zaun angebracht werden mit dem Hinweis, dass das Haus Zu verkaufen ist.
Maße ca. 76 x 244cm
Es darf gerne frech und modern sein mit einem witzigen einladenden Spruch sein, sollte aber auch ansonsten zu meinem chicen Style passen (siehe Homepage www.karwendimmobilien.de) es soll sich abheben von anderen langweiligen Bannern.
Ggf soll die Plane auch noch an einem Tennisplatz angebracht werden

```html
<!DOCTYPE html>
<html lang="de">
<head>
<meta charset="utf-8">
<title>Banner – Karwend Immobilien</title>
<link rel="stylesheet" href="https://fonts.googleapis.com/css2?family=Roboto:wght@400;500;700;900&family=Roboto+Condensed:wght@400;700&display=swap">
<style>
  :root {
    --page: #e6e6e6;
    --ink: #1e1e1e;
    --band: #2b2b2b;
    --gold: #c9a96a;
    --white: #ffffff;
    --wall-light: #f7f7f7;
  }
  * { margin: 0; padding: 0; box-sizing: border-box; }
  html, body { width: 1200px; height: 720px; overflow: hidden; background: var(--page); }
  .banner {
    position: absolute; left: 20px; top: 170px;
    width: 1160px; height: 380px;
    background: var(--wall-light);
    overflow: hidden;
    font-family: "Roboto", Arial, sans-serif;
    color: var(--ink);
    box-shadow: 0 6px 18px rgba(0,0,0,.18);
  }
  .banner-shapes { position: absolute; inset: 0; }
  .headline-light {
    position: absolute; left: 490px; top: 50px;
    font-size: 60px; font-weight: 400; letter-spacing: -0.5px; line-height: 1;
  }
  .headline-bold {
    position: absolute; left: 540px; top: 122px;
    font-size: 63px; font-weight: 900; letter-spacing: -0.5px; line-height: 1;
  }
  .sale-line {
    position: absolute; left: 400px; top: 200px; width: 730px;
    font-family: "Roboto Condensed", Arial, sans-serif;
    font-size: 36px; font-weight: 400; color: var(--white); line-height: 40px;
    white-space: nowrap;
  }
  .sale-line strong { color: var(--gold); font-weight: 700; }
  .contact-bar {
    position: absolute; left: 0; right: 0; bottom: 0; height: 74px;
    padding: 0 150px 0 30px;
    display: flex; align-items: center; justify-content: space-between;
    color: var(--white);
  }
  .contact { display: flex; align-items: center; gap: 10px; white-space: nowrap; }
  .contact svg { flex: none; }
  .contact-phone { font-size: 29px; font-weight: 700; }
  .contact-mail { font-size: 20px; font-weight: 500; }
  .contact-web { font-size: 20px; font-weight: 500; }
  .brand-seal {
    position: absolute; left: 1040px; top: 268px;
    width: 98px; height: 98px; border-radius: 50%;
    background: var(--band);
    display: flex; align-items: center; justify-content: center;
    text-align: center;
    color: var(--white); font-size: 10px; font-weight: 500; letter-spacing: 1px; line-height: 1.3;
  }
</style>
</head>
<body>
  <section class="banner">
    <svg class="banner-shapes" width="1160" height="380" viewBox="0 0 1160 380">
      <defs>
        <linearGradient id="wallShade" x1="0" y1="0" x2="1" y2="1">
          <stop offset="0" stop-color="#ededed"/>
          <stop offset="0.5" stop-color="#fafafa"/>
          <stop offset="1" stop-color="#e2e2e2"/>
        </linearGradient>
        <linearGradient id="photoTone" x1="0" y1="0" x2="1" y2="1">
          <stop offset="0" stop-color="#d9d4cc"/>
          <stop offset="0.45" stop-color="#b89a78"/>
          <stop offset="1" stop-color="#8a6240"/>
        </linearGradient>
      </defs>
      <rect class="wall" x="0" y="0" width="1160" height="380" fill="url(#wallShade)"/>
      <polygon class="photo" points="0,0 459,0 292,306 0,306" fill="url(#photoTone)" role="img" aria-label="Foto: fröhliche Familie beim Umzug, Kind sitzt in einem Umzugskarton"/>
      <polygon class="sale-stripe" points="372,194 1138,194 1134,246 344,246" fill="var(--band)"/>
      <rect class="contact-band" x="0" y="306" width="1160" height="74" fill="var(--band)"/>
    </svg>

    <div class="headline-light">Lust auf einen</div>
    <div class="headline-bold">TAPETENWECHSEL?</div>
    <div class="sale-line">DIESE IMMOBILIE STEHT <strong>ZUM VERKAUF!</strong></div>

    <div class="contact-bar">
      <div class="contact contact-phone">
        <svg width="26" height="26" viewBox="0 0 24 24" aria-hidden="true"><path fill="var(--gold)" d="M6.6 10.8a15.1 15.1 0 0 0 6.6 6.6l2.2-2.2c.3-.3.7-.4 1-.2 1.1.4 2.3.6 3.6.6.6 0 1 .4 1 1V20c0 .6-.4 1-1 1A17 17 0 0 1 3 4c0-.6.4-1 1-1h3.5c.6 0 1 .4 1 1 0 1.3.2 2.5.6 3.6.1.3 0 .7-.2 1z"/></svg>
        <span>02241 / 48 36 217</span>
      </div>
      <div class="contact contact-mail">
        <svg width="24" height="17" viewBox="0 0 26 18" aria-hidden="true"><rect x="0" y="0" width="26" height="18" rx="1" fill="var(--gold)"/><path d="M1 1l12 9 12-9" fill="none" stroke="var(--band)" stroke-width="1.6"/></svg>
        <span>mailrat@karwendimmobilien.de</span>
      </div>
      <div class="contact contact-web">
        <svg width="24" height="24" viewBox="0 0 26 26" aria-hidden="true"><g fill="none" stroke="var(--gold)" stroke-width="1.6"><circle cx="13" cy="13" r="11.5"/><ellipse cx="13" cy="13" rx="5" ry="11.5"/><path d="M1.5 13h23M3.5 7h19M3.5 19h19"/></g></svg>
        <span>www.karwendimmobilien.de</span>
      </div>
    </div>

    <div class="brand-seal">KARWEND<br>IMMOBILIEN</div>
  </section>
</body>
</html>
```